Business Card Design Project

Business Card
We are rebranding with a new logo
Industry/Entity Type
Business
Contact Information for Business Card
Dennis Morvale +61 487215963 dennis@quorv.com.au P.O. Box 872 Fernlow QLD 4309
Requirements
Must have
- Logo

```html
<!DOCTYPE html>
<html lang="en">
<head>
<meta charset="utf-8">
<title>Quorv International – Business Card</title>
<link rel="stylesheet" href="https://fonts.googleapis.com/css2?family=Montserrat:wght@500;600;700&display=swap">
<style>
  :root {
    --backdrop: #c6c6c6;
    --card: #ffffff;
    --ink: #141414;
    --accent: #2aa6df;
    --band-light: #8dd3f3;
    --band-mid: #52bbea;
    --band-deep: #3fa3dd;
    --icon: #6d6d6d;
    --rule: #d9d9d9;
  }
  * { margin: 0; padding: 0; box-sizing: border-box; }
  html, body { width: 1200px; height: 1000px; overflow: hidden; }
  body {
    background: var(--backdrop);
    font-family: "Montserrat", sans-serif;
    position: relative;
  }
  .card {
    position: absolute;
    left: 191px;
    top: 266px;
    width: 818px;
    height: 467px;
    background: var(--card);
    box-shadow: 4px 6px 8px rgba(0,0,0,0.35);
  }
  .brand {
    position: absolute;
    left: 85px;
    top: 186px;
    display: flex;
    align-items: center;
    gap: 12px;
  }
  .brand-dot {
    width: 34px; height: 34px;
    border-radius: 50%;
    background: var(--accent);
  }
  .brand-name {
    font-weight: 700;
    font-size: 20px;
    line-height: 1.25;
    letter-spacing: 1.5px;
    color: var(--ink);
  }
  .holder {
    position: absolute;
    left: 480px;
    top: 65px;
    height: 43px;
    border-left: 3px solid var(--accent);
    padding-left: 24px;
    display: flex;
    align-items: center;
    font-weight: 700;
    font-size: 27px;
    letter-spacing: 1.2px;
    color: var(--ink);
    text-transform: uppercase;
    white-space: nowrap;
  }
  .holder .surname { color: var(--accent); margin-left: 9px; }
  .divider {
    position: absolute;
    left: 417px;
    top: 197px;
    width: 3px;
    height: 106px;
    background: var(--rule);
  }
  .contact-list { list-style: none; }
  .contact {
    position: absolute;
    left: 430px;
    width: 345px;
    height: 52px;
    display: flex;
    align-items: center;
  }
  .contact svg { width: 24px; height: 24px; margin-left: 10px; fill: var(--icon); }
  .contact-band {
    position: absolute;
    left: 47px;
    top: 0;
    width: 298px;
    height: 52px;
    display: flex;
    align-items: center;
    padding-left: 12px;
    color: #fff;
    font-weight: 500;
    font-size: 15.5px;
    letter-spacing: 0.6px;
    white-space: nowrap;
  }
  .contact.phone { top: 154px; }
  .contact.phone .contact-band { background: var(--band-light); }
  .contact.email { top: 210px; }
  .contact.email .contact-band { background: var(--band-mid); }
  .contact.post { top: 265px; }
  .contact.post .contact-band { background: var(--band-deep); padding-left: 10px; }
</style>
</head>
<body>
  <section class="card">
    <div class="brand">
      <span class="brand-dot"></span>
      <span class="brand-name">QUORV<br>INTERNATIONAL</span>
    </div>

    <h1 class="holder">Dennis<span class="surname">Morvale</span></h1>

    <span class="divider"></span>

    <ul class="contact-list">
      <li class="contact phone">
        <svg viewBox="0 0 24 24" aria-hidden="true"><path d="M6.6 10.8c1.4 2.8 3.8 5.1 6.6 6.6l2.2-2.2c.3-.3.7-.4 1-.2 1.1.4 2.3.6 3.6.6.6 0 1 .4 1 1V20c0 .6-.4 1-1 1C10.6 21 3 13.4 3 4c0-.6.4-1 1-1h3.5c.6 0 1 .4 1 1 0 1.3.2 2.5.6 3.6.1.3 0 .7-.2 1l-2.3 2.2z"/></svg>
        <span class="contact-band">+61 487215963</span>
      </li>
      <li class="contact email">
        <svg viewBox="0 0 24 24" aria-hidden="true"><path d="M2 5h20v14H2z M3.5 6.5 12 12.5l8.5-6z" fill-rule="evenodd"/></svg>
        <span class="contact-band">dennis@quorv.com.au</span>
      </li>
      <li class="contact post">
        <svg viewBox="0 0 24 24" aria-hidden="true"><path fill="none" stroke="#6d6d6d" stroke-width="1.6" d="M12 2.8a9.2 9.2 0 1 0 0 18.4a9.2 9.2 0 1 0 0-18.4zM2.8 12h18.4M12 2.8c-3 3-3 15.4 0 18.4M12 2.8c3 3 3 15.4 0 18.4M4.2 7.2h15.6M4.2 16.8h15.6"/></svg>
        <span class="contact-band">P.O. Box 872 Fernlow QLD 4309</span>
      </li>
    </ul>
  </section>
</body>
</html>
```